Banner to be displayed at local Farmers Market Booth.

Graphic Design Brief: Farmers Market Banner Contest

Project Overview:We are seeking talented graphic designers to create a visually appealing banner for our booth at the local farmers market. Our company specializes in healthy, all-natural dog and cat treats, and we want a banner that captures our brand identity while drawing in pet owners who value quality and nutrition for their furry friends.

Banner Specifications:

Size: 24 inches x 60 inches (Horizontal orientation) 24" High X 60 wide

Theme: Vintage/Retro

Style: Warm, inviting, nostalgic with a touch of rustic charm

Colors: Earthy, muted tones such as warm browns, soft greens, and creamy yellows. Pops of red or blue may be used sparingly for accents. OR Black and White with gray scales. Would like to see both

Typography: Retro-style fonts that are readable and align with the vintage aesthetic.

Key Elements to Include: website (www.moltbyfarms.com)

Company Name: Moltby Farms

Tagline: " Simply Honest Bites "
Imagery: Illustrations or stylized graphics of happy dogs and cats, possibly interacting with treats.

Emphasis on Natural Ingredients: Icons or design elements that subtly suggest freshness and quality (e.g., leaves, wheat, bones, or paw prints).

Farmers Market Appeal: A design that blends well with the artisanal, handmade, and farm-fresh atmosphere of the market.

Design Considerations:

The banner should be easily readable from a distance.

A balanced composition that doesn't feel overcrowded.

Should evoke trust and warmth while maintaining a professional look.

Avoid overly modern or sleek elements that don’t align with the vintage aesthetic.

Submission Requirements:

High-resolution digital file in PDF or AI format.

CMYK color mode for printing purposes.

Must include a mockup or preview of how it would look in a real farmers market setting.

We look forward to seeing your creative interpretations of our brand! If you have any questions, feel free to reach out.

Font styles to use
Other font styles liked:
• See attachement

Requirements
Nice to have
• Retro/Vintage,playful BUT NOT whimsical

```html
<!DOCTYPE html>
<html lang="en">
<head>
<meta charset="utf-8">
<title>Moltby Farms — Market Banner</title>
<link rel="stylesheet" href="https://fonts.googleapis.com/css2?family=Russo+One&family=Libre+Baskerville:wght@400;700&display=swap">
<style>
  :root {
    --stage: #e9e6e1;
    --ink: #0e0e0e;
    --paper: #ffffff;
    --orange: #f5861f;
    --sketch-light: #f3f3f1;
    --sketch-mid: #bdbdb8;
    --logo-ink: #1a1a1a;
  }
  html, body {
    margin: 0;
    padding: 0;
    width: 1200px;
    height: 944px;
    overflow: hidden;
    background: var(--stage);
  }
  .banner {
    position: absolute;
    left: 0;
    top: 232px;
    width: 1200px;
    height: 480px;
    display: block;
  }
  .banner-bg-dark { fill: var(--ink); }
  .banner-bg-orange { fill: var(--orange); }
  .torn-edge { fill: var(--paper); }
  .brand-title {
    font-family: "Russo One", sans-serif;
    fill: var(--paper);
  }
  .web-address {
    font-family: "Libre Baskerville", serif;
    fill: var(--paper);
    letter-spacing: 4px;
  }
  .tagline {
    font-family: "Libre Baskerville", serif;
    font-weight: 700;
    fill: var(--paper);
  }
  .tagline-shadow {
    font-family: "Libre Baskerville", serif;
    font-weight: 700;
    fill: var(--ink);
  }
  .descriptor {
    font-family: "Libre Baskerville", serif;
    fill: var(--paper);
  }
  .mascot-art {
    fill: url(#sketchTone);
  }
  .art-logo-name {
    font-family: "Libre Baskerville", serif;
    font-weight: 400;
    fill: var(--logo-ink);
  }
  .art-logo-dot { fill: var(--logo-ink); }
</style>
</head>
<body>
<svg class="banner" viewBox="0 0 1200 480" xmlns="http://www.w3.org/2000/svg">
  <defs>
    <radialGradient id="sketchTone" cx="55%" cy="55%" r="70%">
      <stop offset="0%" stop-color="#d4d4cf"/>
      <stop offset="100%" stop-color="#f3f3f1"/>
    </radialGradient>
  </defs>

  <rect class="banner-bg-orange" x="0" y="0" width="1200" height="480"/>

  <path class="torn-edge" d="M0 0 H1200 V330 L1170 336 L1140 332 L1110 352 L1080 348 L1050 360 L1020 356 L990 370 L960 362 L930 372 L900 360 L870 366 L840 356 L810 352 L790 330 L760 322 L730 312 L700 322 L660 304 L630 316 L600 318 L570 312 L540 302 L520 300 L500 308 L470 298 L445 302 L420 296 L395 306 L370 312 L345 304 L320 298 L300 288 L270 306 L240 300 L210 292 L180 298 L150 304 L120 294 L90 300 L60 298 L30 304 L0 300 Z"/>
  <path class="banner-bg-dark" d="M0 0 H1200 V326 L1170 332 L1140 328 L1110 348 L1080 344 L1050 356 L1020 352 L990 366 L960 358 L930 368 L900 356 L870 362 L840 352 L810 348 L790 326 L760 318 L730 308 L700 318 L660 300 L630 312 L600 314 L570 308 L540 298 L520 296 L500 304 L470 294 L445 298 L420 292 L395 302 L370 308 L345 300 L320 294 L300 284 L270 302 L240 296 L210 288 L180 294 L150 300 L120 290 L90 296 L60 294 L30 300 L0 296 Z"/>

  <text class="brand-title" x="57" y="144" font-size="118" textLength="695" lengthAdjust="spacingAndGlyphs">MOLTBY</text>
  <text class="brand-title" x="57" y="232" font-size="92" textLength="695" lengthAdjust="spacingAndGlyphs">FARMS</text>

  <text class="web-address" x="110" y="282" font-size="25" textLength="582" lengthAdjust="spacing">WWW.MOLTBYFARMS.COM</text>

  <rect class="mascot-art" x="811" y="17" width="327" height="345" role="img" aria-label="Pencil sketch of a dog and a cat sitting together on a rock ledge"/>
  <circle class="art-logo-dot" cx="990" cy="58" r="5"/>
  <text class="art-logo-name" x="1002" y="64" font-size="16">Moltby Farms</text>

  <text class="tagline-shadow" x="64" y="406" font-size="52" textLength="700" lengthAdjust="spacingAndGlyphs">SIMPLY HONEST BITES</text>
  <text class="tagline" x="61" y="403" font-size="52" textLength="700" lengthAdjust="spacingAndGlyphs">SIMPLY HONEST BITES</text>

  <text class="descriptor" x="64" y="455" font-size="40" textLength="1086" lengthAdjust="spacingAndGlyphs">PURVEYORS OF PREMIUM PET FOOD &amp; TREATS</text>
</svg>
</body>
</html>
```